Exciting & Elegant Stationary Pack

Stationary consists of
1. Letter head / Envelope
2. Business Card
3. Invoice
4. 40x40mm sticker

Attached files;

1. Logo (Other formats available on request)
2. MS word Doc - For information and description of design
3. Website image (This will be our new website so use the colours so everything ties together)
4. Sample of stationary pack we like, but feel free to be creative

Target Market(s)

Home improvement

Industry/Entity Type

Construction

Font styles to use
Other font styles liked:
• Leave up to designer - We like font used on (website attached image)

Requirements
Must have
• Please look at uploaded file of sample website and use colours
Nice to have
• Any type of business card design - eg. metal, die cut, embossed, etc...

```html
<!DOCTYPE html>
<html lang="en">
<head>
<meta charset="utf-8">
<title>Grout Line Envelope Set</title>
<link rel="stylesheet" href="https://fonts.googleapis.com/css2?family=Open+Sans:wght@400;800&display=swap">
<style>
  :root {
    --navy: #0f4468;
    --red: #d1282e;
    --sky: #a9c8e3;
    --paper: #f4f3f1;
    --backdrop: #a3a3a3;
    --ink: #16222c;
  }
  * { margin: 0; padding: 0; box-sizing: border-box; }
  html, body { width: 1200px; height: 198px; overflow: hidden; background: var(--backdrop); }
  body { position: relative; font-family: "Open Sans", sans-serif; }

  .envelope {
    position: absolute;
    top: 15px;
    height: 168px;
    background: var(--paper);
    overflow: hidden;
  }
  .envelope--front { left: 10px; width: 367px; }
  .envelope--back-open { left: 416px; width: 363px; }
  .envelope--back-closed { left: 818px; width: 375px; }

  .brand-name {
    position: absolute;
    display: flex;
    align-items: center;
    gap: 5px;
    font-weight: 800;
    font-size: 15px;
    letter-spacing: 0.5px;
    line-height: 1;
    white-space: nowrap;
  }
  .brand-name__square { width: 10px; height: 10px; background: currentColor; }

  /* front */
  .front__brand { left: 20px; top: 112px; color: var(--navy); }
  .front__red-band { position: absolute; left: 0; right: 0; top: 126px; height: 15px; background: var(--red); }
  .front__address-band {
    position: absolute; left: 0; right: 0; top: 141px; bottom: 0;
    background: var(--sky);
    display: flex; align-items: center; gap: 5px;
    padding-left: 22px;
    font-size: 7px; color: var(--ink);
  }
  .front__address-band svg { width: 7px; height: 10px; }

  /* open back */
  .open__flap {
    position: absolute; left: 3px; right: 3px; top: 0; height: 52px;
    background: var(--navy);
    border-radius: 0 0 12px 12px;
  }
  .open__brand { left: 50%; transform: translateX(-50%); top: 14px; color: var(--paper); }

  /* closed back */
  .closed__navy { position: absolute; left: 0; right: 0; top: 0; height: 26px; background: var(--navy); }
  .closed__red { position: absolute; left: 0; right: 0; top: 26px; height: 15px; background: var(--red); }
  .closed__sky {
    position: absolute; left: 0; right: 0; top: 41px; height: 11px;
    background: var(--sky); border-radius: 0 0 12px 12px;
  }
  .closed__brand { right: 28px; top: 6px; color: var(--paper); }
</style>
</head>
<body>
  <section class="envelope envelope--front" aria-label="Envelope front">
    <div class="brand-name front__brand"><span class="brand-name__square"></span>GROUT LINE</div>
    <div class="front__red-band"></div>
    <div class="front__address-band">
      <svg viewBox="0 0 10 14" aria-hidden="true"><path d="M5 0C2.2 0 0 2.2 0 5c0 3.6 5 9 5 9s5-5.4 5-9c0-2.8-2.2-5-5-5zm0 7a2 2 0 1 1 0-4 2 2 0 0 1 0 4z" fill="var(--ink)"/></svg>
      <span class="address-line">PO Box 48 Fairview Park NSW 2170</span>
    </div>
  </section>

  <section class="envelope envelope--back-open" aria-label="Envelope back, flap open">
    <div class="open__flap"></div>
    <div class="brand-name open__brand"><span class="brand-name__square"></span>GROUT LINE</div>
  </section>

  <section class="envelope envelope--back-closed" aria-label="Envelope back, flap closed">
    <div class="closed__sky"></div>
    <div class="closed__red"></div>
    <div class="closed__navy"></div>
    <div class="brand-name closed__brand"><span class="brand-name__square"></span>GROUT LINE</div>
  </section>
</body>
</html>
```